Pastor's Lantern: How To Help Church Leaders Remain Strong In Their Callings.

I have created a 250-page book tentatively entitled, Pastor's Lantern, subtitle: A Handbook To Help Church Leaders Remain Strong in Their Callings. The chapters are taken from my podcast of the same name on TuneVault and website: pastorslantern-example.com which will need updating soon. The purpose of the book is to provide practical solutions to pastors/leaders about everyday issues faced in ministry such as loneliness, financial challenges, a pastor's family problems, sexual temptation ...etc. You can get an idea of the topics from TuneVault.
Updates

As mentioned in the brief, I am looking for something that will communicate solutions. My podcast, Pastor's Lantern from which this material originates is all about practical help for local pastors in facing the challenges of daily ministry. The logo I sent was designed for concept purposes only. It does not need to be on the cover necessarily unless it feeds into the overall theme.

Target Market(s)

Pastors and Church Leaders in the Christian Faith

Industry/Entity Type

Religious

Font styles to use
Serif

Colors

Designer to choose colors to be used in the design.

Requirements
Must have
• Crisp copy and lines. People see covers for 3 seconds. If they are not drawn in by complicated themes, I have failed. Many of the designs so far do not address the topic of the book in a way that impacts. This is about a toolbox or book that provides solutions to their everyday challenges. If it doesn't somehow point to tools, it should instead point to getting solutions.
Nice to have
• I have included a copy of my current logo. If you can incorporate it, fine. If you have a better idea, I am open to that and would be interested in contributing more if the logo is superior. The logo is not essential to either front or back cover..
Should not have
• Simplistic religious themes from often used pics. I will peruse other book covers in my genre. If I find the same pic used, it disqualifies the design immediately no matter how much I like it. Target audience is ministers. Simplistic cross designs have gotten less votes so far in polling. I want to grab attention with a compelling picture that communicates solutions.

```html
<!DOCTYPE html>
<html lang="en">
<head>
<meta charset="utf-8">
<title>Pastor's Lantern – Book Cover</title>
<link href="https://fonts.googleapis.com/css2?family=Cinzel:wght@400;500&display=swap" rel="stylesheet">
<style>
  :root {
    --sky-top: #1665b3;
    --sky-mid: #1f74bf;
    --sky-low: #4a8dcc;
    --hill: #0a0b0d;
    --scene-dark: #0c0e12;
    --ink-light: #ffffff;
  }
  html, body {
    margin: 0;
    padding: 0;
    width: 941px;
    height: 1200px;
    overflow: hidden;
    background: var(--hill);
  }
  .cover {
    position: relative;
    width: 941px;
    height: 1200px;
    overflow: hidden;
    background: linear-gradient(180deg, var(--sky-top) 0%, var(--sky-mid) 40%, var(--sky-low) 85%);
    font-family: "Cinzel", "Trajan Pro", Georgia, serif;
    color: var(--ink-light);
  }
  .cover-art {
    position: absolute;
    left: 0;
    top: 0;
    width: 941px;
    height: 1200px;
  }
  .title-block {
    position: absolute;
    left: 0;
    right: 0;
    top: 58px;
    text-align: center;
  }
  .title-kicker {
    margin: 0;
    font-size: 66px;
    font-weight: 400;
    letter-spacing: 0.46em;
    padding-left: 0.46em;
    line-height: 1;
  }
  .title-main {
    margin: 12px 0 0;
    font-size: 128px;
    font-weight: 400;
    letter-spacing: 0.04em;
    padding-left: 0.04em;
    line-height: 1;
  }
  .subtitle {
    margin: 78px 0 0;
    font-size: 28px;
    font-weight: 400;
    line-height: 1.2;
    letter-spacing: 0.03em;
  }
  .author {
    position: absolute;
    left: 0;
    right: 0;
    top: 1086px;
    margin: 0;
    text-align: center;
    font-size: 44px;
    font-weight: 400;
    line-height: 1;
    letter-spacing: 0.26em;
    padding-left: 0.26em;
  }
</style>
</head>
<body>
  <main class="cover">
    <svg class="cover-art" viewBox="0 0 941 1200" aria-hidden="true">
      <path d="M0,552 C230,790 540,960 941,1031 L941,1200 L0,1200 Z" fill="var(--hill)"/>
    </svg>

    <svg class="cover-art scene" viewBox="0 0 941 1200" role="img" aria-label="Silhouette of a figure pushing a large boulder up the dark hillside, symbolising the daily struggle of ministry">
      <rect x="12" y="432" width="310" height="370" rx="10" fill="var(--scene-dark)" opacity="0.9"/>
    </svg>

    <header class="title-block">
      <p class="title-kicker">PASTOR'S</p>
      <h1 class="title-main">LANTERN</h1>
      <p class="subtitle">A HANDBOOK TO HELP CHURCH LEADERS<br>REMAIN STRONG IN THEIR CALLINGS</p>
    </header>

    <p class="author">COREY M. SANDELL</p>
  </main>
</body>
</html>
```